Brightway Haul & Upkeep Services, are a company that offers a 'one stop shop' pre-move clean up a

I have already selected a logo which I would like on the front of the business cards along with phone numbers, web address and email which are:
0487650392
www.brightwayhaul.com.au
brightwayhaulandupkeep@mailbox.example

On the back of the card I would like to list some of the types of service we offer (clean - move - repairs/maintenance) which are:
CLEAN - windows, gutters, solar panels, driveways/paths, carpets.
MOVE - Small/medium size house/office moves, large item pick-up & delivery, yard clean-up and removal.
General maintenance and repairs.

I would like the blue logo on a gray background.

Thanks

```html
<!DOCTYPE html>
<html lang="en">
<head>
<meta charset="utf-8">
<title>Brightway Haul &amp; Upkeep Services — Business Card</title>
<link rel="stylesheet" href="https://fonts.googleapis.com/css2?family=Open+Sans:wght@400;600;700;800&display=swap">
<style>
  :root {
    --stage: #e9e9e9;
    --silver-light: #f4f4f4;
    --silver-mid: #d6d6d6;
    --silver-dark: #a9a9a9;
    --brand-blue: #2a6fc0;
    --band-black: #232323;
    --ink: #2b2b2b;
    --white: #ffffff;
  }
  * { box-sizing: border-box; margin: 0; padding: 0; }
  html, body { width: 1200px; height: 765px; overflow: hidden; }
  body {
    background: var(--stage);
    font-family: "Open Sans", Arial, sans-serif;
    position: relative;
  }
  .card {
    position: absolute;
    width: 540px;
    height: 310px;
    border-radius: 22px;
    overflow: hidden;
    background: radial-gradient(ellipse at 45% 40%, var(--silver-light) 0%, var(--silver-mid) 55%, var(--silver-dark) 100%);
    box-shadow: 0 10px 24px rgba(0,0,0,0.22);
  }
  .card--front { left: 40px; top: 110px; }
  .card--back { left: 620px; top: 345px; }

  .brand-name {
    color: var(--brand-blue);
    font-weight: 800;
    line-height: 1.05;
    letter-spacing: -0.5px;
  }
  .card--front .brand-name {
    position: absolute;
    left: 42px;
    top: 58px;
    width: 340px;
    font-size: 34px;
  }

  .front-bands { position: absolute; left: 0; bottom: 0; width: 540px; height: 150px; }
  .contact-list {
    position: absolute;
    left: 32px;
    top: 188px;
    list-style: none;
    font-size: 12.5px;
    color: var(--ink);
  }
  .contact-list li { display: flex; align-items: center; gap: 7px; margin-bottom: 6px; }
  .contact-icon { width: 12px; height: 12px; flex: none; }
  .web-strip {
    position: absolute;
    left: 32px;
    bottom: 18px;
    color: var(--white);
    font-size: 13px;
    font-weight: 600;
    letter-spacing: 3.2px;
  }

  .card--back .brand-name {
    position: absolute;
    left: 0;
    right: 0;
    top: 54px;
    text-align: center;
    font-size: 34px;
  }
  .services-title {
    position: absolute;
    left: 0; right: 0;
    top: 160px;
    text-align: center;
    color: var(--brand-blue);
    font-size: 20px;
    font-weight: 600;
    letter-spacing: 6px;
  }
  .service-list {
    position: absolute;
    left: 0; right: 0;
    top: 200px;
    text-align: center;
    list-style: none;
    color: var(--band-black);
    font-size: 19px;
    font-weight: 600;
    line-height: 1.35;
  }
  .service-list .pair span + span { margin-left: 26px; }
  .service-list span::before { content: "• "; }
</style>
</head>
<body>

  <section class="card card--front" aria-label="Business card front">
    <p class="brand-name">Brightway Haul &amp; Upkeep Services</p>

    <svg class="front-bands" viewBox="0 0 540 150" preserveAspectRatio="none" aria-hidden="true">
      <path d="M0 150 L0 122 L330 122 C380 122 390 60 430 50 L540 38 L540 150 Z" fill="var(--band-black)"/>
      <path d="M0 150 L0 122 L300 112 C350 110 370 74 410 68 L540 56 L540 70 L420 82 C385 86 365 122 320 128 L0 136 Z" fill="var(--brand-blue)"/>
      <path d="M0 150 L0 126 L330 120 C350 119 360 112 372 104 L372 150 Z" fill="var(--brand-blue)"/>
    </svg>

    <ul class="contact-list">
      <li>
        <svg class="contact-icon" viewBox="0 0 12 12" aria-hidden="true"><path d="M3 1 L5 3.5 L4 5 C4.6 6.4 5.6 7.4 7 8 L8.5 7 L11 9 L10 11 C5 11 1 7 1 2 Z" fill="var(--brand-blue)"/></svg>
        <span>0487650392</span>
      </li>
      <li>
        <svg class="contact-icon" viewBox="0 0 12 12" aria-hidden="true"><rect x="1" y="2.5" width="10" height="7" rx="1" fill="var(--brand-blue)"/><path d="M1.5 3 L6 6.5 L10.5 3" stroke="var(--white)" stroke-width="1" fill="none"/></svg>
        <span>brightwayhaulandupkeep@mailbox.example</span>
      </li>
      <li>
        <svg class="contact-icon" viewBox="0 0 12 12" aria-hidden="true"><circle cx="6" cy="6" r="5" fill="none" stroke="var(--brand-blue)" stroke-width="1.3"/><path d="M1 6 H11 M6 1 C3.5 4 3.5 8 6 11 M6 1 C8.5 4 8.5 8 6 11" stroke="var(--brand-blue)" stroke-width="1" fill="none"/></svg>
        <span>brightwayhaul.com.au</span>
      </li>
    </ul>

    <p class="web-strip">www.brightwayhaul.com.au</p>
  </section>

  <section class="card card--back" aria-label="Business card back">
    <p class="brand-name">Brightway Haul &amp; Upkeep Services</p>
    <h2 class="services-title">Services we offer</h2>
    <ul class="service-list">
      <li class="pair"><span>Clean</span><span>Move</span></li>
      <li><span>General maintenance and repairs.</span></li>
    </ul>
  </section>

</body>
</html>
```